Website for new slot-booking/reservations website/software

For a new software product we need a brand new logo and website for a reservations/booking system. The website should ideally present the main features with information text, contact info, news page as well as registration and pricing pages. As currently primary field of operation the software should be used for tennis but later on, also for other sport types. Also we'd like to be the logo a text-brand which includes the name "zeitfeldo.com" or just "zeitfeldo". The logo should ideally include an icon-design in some way. Generally we are open for ideas.

Bootstrap 4 template is a minimum requirement. (Multi-Page preferred, Single-Page still OK.)

You can use the attached image as an inspiration, but change of colors or other design elements are up to you. Currently the application has a primary color of #5500ff. The website created by you will not include the application itself, so it can have different (but ideally similar) Look&Feel.
Updates

Target Market(s)

Sports, Club-Management

Logo Text

zeitfeldo.com

Coding

Coded - Design and coding required

Number of Pages Required

5+ page

Font styles to use
Sans Serif

Requirements
Must have
• Bootstrap 4 Template, SCSS
Nice to have
• Rapid Loading Times, not too much external JS Libraries.
Should not have
• Extensive animations

```html
<!DOCTYPE html>
<html lang="en">
<head>
<meta charset="utf-8">
<title>zeitfeldo – Booking system</title>
<link href="https://fonts.googleapis.com/css2?family=Poppins:wght@400;500;600&family=Raleway:wght@300;400;500;700&display=swap" rel="stylesheet">
<style>
:root{
  --purple:#5500ff;
  --violet:#6a3df0;
  --deep:#4b1fb8;
  --lavender:#9b8cf2;
  --pill:#ececf2;
  --ink:#14141f;
  --text:#4a4a55;
  --muted:#8c8c99;
  --cyan:#10d8ee;
  --cyan-soft:#e6fbfd;
  --read:#efeafd;
  --white:#ffffff;
}
*{box-sizing:border-box;margin:0;padding:0}
html,body{width:1200px;height:3797px;overflow:hidden}
body{position:relative;background:var(--white);font-family:"Raleway",sans-serif;color:var(--text)}
.abs{position:absolute}

/* nav */
.nav{position:absolute;left:0;top:0;width:1200px;height:88px;background:var(--white);z-index:3}
.brand{position:absolute;left:96px;top:30px;display:flex;align-items:center;gap:8px;font-family:"Poppins",sans-serif;font-size:22px;font-weight:500;color:var(--violet)}
.brand .dot{width:20px;height:20px;border-radius:50%;background:var(--violet)}
.nav-link{position:absolute;top:35px;font-family:"Poppins",sans-serif;font-size:16px;color:#333}
.nav-link.active{color:var(--purple);font-weight:500}
.login{position:absolute;left:996px;top:29px;width:96px;height:33px;border:2px solid var(--purple);border-radius:17px;color:var(--purple);font-family:"Poppins",sans-serif;font-size:15px;text-align:center;line-height:29px}

/* hero */
.hero-bg{position:absolute;left:0;top:88px;width:1200px;height:640px}
.hero-title{left:98px;top:206px;font-family:"Poppins",sans-serif;font-weight:600;font-size:50px;line-height:60px;color:var(--white);z-index:2}
.hero-sub{left:98px;top:274px;font-family:"Poppins",sans-serif;font-weight:500;font-size:32px;line-height:38px;color:var(--white);z-index:2}
.hero-lead{left:99px;top:364px;font-family:"Poppins",sans-serif;font-size:24px;line-height:30px;color:var(--white);z-index:2;width:470px}
.btn-hero{position:absolute;top:454px;height:44px;border-radius:22px;font-family:"Poppins",sans-serif;font-size:15px;text-align:center;line-height:42px;z-index:2}
.btn-register{left:99px;width:132px;background:var(--white);color:var(--deep);font-weight:600}
.btn-learn{left:252px;width:131px;border:2px solid var(--white);color:var(--white);line-height:40px}
.photo{position:absolute;z-index:1}

/* sections */
.pill{position:absolute;height:44px;width:178px;border-radius:22px;background:var(--pill);color:var(--purple);font-family:"Poppins",sans-serif;font-size:13px;text-align:center;line-height:44px}
.section-title{position:absolute;font-family:"Poppins",sans-serif;font-weight:600;font-size:25px;line-height:30px;color:var(--ink)}
.section-text{position:absolute;font-size:16.5px;line-height:19.5px;color:var(--text)}

.feature{position:absolute;width:430px}
.feature .tick{position:absolute;left:0;top:-4px;width:30px;height:30px}
.feature h3{margin-left:44px;font-family:"Poppins",sans-serif;font-weight:400;font-size:17px;color:var(--ink)}
.feature p{margin-left:44px;margin-top:14px;font-size:16.5px;line-height:19.5px;color:var(--text)}

.about-text{position:absolute;left:99px;top:1592px;width:480px;font-weight:300;font-size:26px;line-height:29.3px;color:#333}
.about-text p+p{margin-top:29px}

/* pricing */
.plan{position:absolute;width:200px;font-family:"Poppins",sans-serif}
.plan .price{font-size:30px;font-weight:500;color:var(--ink)}
.plan .price small{font-size:13px;font-weight:400;color:var(--muted);margin-left:6px}
.plan .name{margin-top:16px;font-size:24px;font-weight:500;color:var(--ink)}
.plan .desc{margin-top:10px;font-size:12px;line-height:16px;color:var(--muted);font-family:"Raleway",sans-serif}
.plan ul{list-style:none;margin-top:18px}
.plan li{height:26px;font-size:12.5px;color:var(--muted);display:flex;align-items:center;gap:9px;font-family:"Raleway",sans-serif}
.plan li svg{flex:none}
.plan .choose{margin-top:16px;width:172px;height:36px;border-radius:6px;background:var(--cyan-soft);color:var(--cyan);font-size:13px;text-align:center;line-height:36px}
.plan-pro{left:588px;top:2252px;width:242px;height:398px;border-radius:8px;background:var(--violet);box-shadow:0 24px 40px rgba(106,61,240,.3);padding:36px 25px 0}
.plan-pro .price,.plan-pro .name,.plan-pro .price small{color:var(--white)}
.plan-pro .desc,.plan-pro li{color:#e9e4ff}
.plan-pro .choose{width:192px;background:var(--cyan);color:var(--deep)}
.badge{position:absolute;left:125px;top:19px;width:98px;height:18px;border-radius:9px;background:#4d22c9;color:#cfc4ff;font-size:9px;letter-spacing:1px;text-align:center;line-height:18px}

/* news */
.news-card{position:absolute;width:302px}
.news-img{width:302px;height:188px}
.news-card h4{margin:30px 0 0 19px;font-family:"Poppins",sans-serif;font-weight:500;font-size:16px;line-height:19px;color:var(--ink)}
.news-card p{margin:14px 0 0 19px;width:260px;font-size:16.5px;line-height:19px;color:var(--text)}
.read-more{margin:22px 0 0 19px;width:172px;height:36px;border-radius:6px;background:var(--read);color:var(--violet);font-family:"Poppins",sans-serif;font-size:13px;text-align:center;line-height:36px}

/* footer */
.footer-bg{position:absolute;left:0;top:3320px;width:1200px;height:477px}
.footer-brand{left:88px;top:3496px;display:flex;align-items:center;gap:10px;font-family:"Poppins",sans-serif;font-weight:500;font-size:34px;color:var(--white)}
.footer-brand .dot{width:30px;height:30px;border-radius:50%;background:var(--white)}
.footer-tag{left:88px;top:3560px;width:430px;font-weight:700;font-size:19px;line-height:26px;color:#b4a6f7}
.footer-col{position:absolute;top:3500px;font-family:"Poppins",sans-serif;font-size:15px;color:var(--white)}
.footer-col h5{font-weight:400;font-size:15px;color:#b8acf3;margin-bottom:38px}
.footer-col li{list-style:none;line-height:23.5px}
.copyright{left:88px;top:3733px;font-size:14px;color:#b4a6f7}
.terms{left:998px;top:3733px;font-family:"Poppins",sans-serif;font-weight:600;font-size:14px;color:var(--white)}
.footer-art{position:absolute;border-radius:12px;background:linear-gradient(135deg,rgba(255,255,255,.35),rgba(155,140,242,.25))}
</style>
</head>
<body>

<header class="nav">
  <div class="brand"><span class="dot"></span>zeitfeldo</div>
  <span class="nav-link active" style="left:601px">Home</span>
  <span class="nav-link" style="left:699px">Templates</span>
  <span class="nav-link" style="left:831px">Price</span>
  <span class="nav-link" style="left:920px">Help</span>
  <span class="login">Login</span>
</header>

<svg class="hero-bg" viewBox="0 0 1200 640" aria-hidden="true">
  <defs>
    <linearGradient id="heroGrad" x1="0" y1="0" x2="1" y2="1">
      <stop offset="0" stop-color="#6b1fc8"/>
      <stop offset=".55" stop-color="#6a3df0"/>
      <stop offset="1" stop-color="#5a2bd8"/>
    </linearGradient>
  </defs>
  <path d="M0 620 C120 640 240 640 420 600 C620 560 760 560 1000 590 C1100 600 1160 590 1200 585 V560 C1000 575 900 520 720 510 C500 500 300 600 120 580 C60 572 20 560 0 540 Z" fill="#9d8ef2"/>
  <path d="M0 0 H1200 V580 C1050 560 920 480 720 480 C520 480 360 590 180 570 C90 560 30 530 0 500 Z" fill="url(#heroGrad)"/>
</svg>

<h1 class="abs hero-title">Booking system</h1>
<div class="abs hero-sub">for sports, gyms, classes<br>and more</div>
<p class="abs hero-lead">Easy to use and customisable online booking system you can trust</p>
<span class="btn-hero btn-register">Register now</span>
<span class="btn-hero btn-learn">Learn more</span>

<div class="photo" role="img" aria-label="Tennis player in a green shirt holding a racket" style="left:572px;top:295px;width:194px;height:339px;background:linear-gradient(180deg,#a392f0,#7a5fe4);border-radius:90px 90px 10px 10px"></div>
<div class="photo" role="img" aria-label="Tennis player in a purple shirt about to serve" style="left:796px;top:147px;width:404px;height:516px;background:linear-gradient(160deg,#8b6bf2,#4d22b9);border-radius:200px 0 0 40px"></div>
<div class="photo" role="img" aria-label="Phone and laptop showing the booking app pricing screen" style="left:719px;top:646px;width:364px;height:162px;background:linear-gradient(180deg,#e9e6f7,#c9c3e8);border-radius:10px"></div>

<span class="pill" style="left:99px;top:764px">FEATURES</span>
<h2 class="section-title" style="left:98px;top:827px">Online Booking System for<br>Individual Reservations</h2>
<p class="section-text" style="left:97px;top:903px;width:420px">The system allows one booking during the time. It is possible to set-up different prices based on peak or off-peak periods. The system uses different colours, where colours can be different for each person or booking status.</p>

<div class="feature" style="left:99px;top:1048px">
  <svg class="tick" viewBox="0 0 30 30"><circle cx="15" cy="15" r="15" fill="#efeefe"/><path d="M9 15.5l4 4 8-9" fill="none" stroke="#5500ff" stroke-width="2"/></svg>
  <h3>Better Management of Multi-Function Halls</h3>
  <p>Multi-function halls; for example, a hall can be used for the whole court of basketball or 2 courts of badminton, the system now sees the relationship between bookings.</p>
</div>
<div class="feature" style="left:581px;top:1048px">
  <svg class="tick" viewBox="0 0 30 30"><circle cx="15" cy="15" r="15" fill="#efeefe"/><path d="M9 15.5l4 4 8-9" fill="none" stroke="#5500ff" stroke-width="2"/></svg>
  <h3>Better Management of Multi-Function Halls</h3>
  <p>Multi-function halls; for example, a hall can be used for the whole court of basketball or 2 courts of badminton, the system now sees the relationship between bookings.</p>
</div>
<div class="feature" style="left:99px;top:1205px">
  <svg class="tick" viewBox="0 0 30 30"><circle cx="15" cy="15" r="15" fill="#efeefe"/><path d="M9 15.5l4 4 8-9" fill="none" stroke="#5500ff" stroke-width="2"/></svg>
  <h3>Better Management of Multi-Function Halls</h3>
  <p>Multi-function halls; for example, a hall can be used for the whole court of basketball or 2 courts of badminton, the system now sees the relationship between bookings.</p>
</div>
<div class="feature" style="left:581px;top:1205px">
  <svg class="tick" viewBox="0 0 30 30"><circle cx="15" cy="15" r="15" fill="#efeefe"/><path d="M9 15.5l4 4 8-9" fill="none" stroke="#5500ff" stroke-width="2"/></svg>
  <h3>Better Management of Multi-Function Halls</h3>
  <p>Multi-function halls; for example, a hall can be used for the whole court of basketball or 2 courts of badminton, the system now sees the relationship between bookings.</p>
</div>

<div class="abs" role="img" aria-label="Faint decorative line pattern" style="left:1000px;top:1165px;width:200px;height:470px;background:linear-gradient(200deg,rgba(155,140,242,.18),rgba(155,140,242,0))"></div>

<span class="pill" style="left:99px;top:1449px">zeitfeldo</span>
<h2 class="section-title" style="left:99px;top:1511px">About zeitfeldo<br>Booking System</h2>
<div class="about-text">
  <p>zeitfeldo booking system has been created to help gyms, sport centres and other businesses to manage bookings online. It can be used to manage creche in gyms, group activities or individual sports like badminton or tennis.</p>
  <p>Our system is easy to use for both business owners and end-users. We have a wide range of settings that customise system to your needs. You can check out some of our testimonials.</p>
</div>

<span class="pill" style="left:111px;top:2067px">Pricing</span>
<h2 class="section-title" style="left:111px;top:2128px">Find the perfect plan that<br>fits for you.</h2>

<div class="plan" style="left:144px;top:2328px">
  <div class="price">$20<small>/month</small></div>
  <div class="name">Intro</div>
  <div class="desc">For most businesses that want to otpimize web queries</div>
  <ul>
    <li><svg width="14" height="14" viewBox="0 0 14 14"><circle cx="7" cy="7" r="7" fill="#ecebf7"/><path d="M4 7.2l2 2 4-4.4" fill="none" stroke="#6a3df0" stroke-width="1.4"/></svg>All limited links</li>
    <li><svg width="14" height="14" viewBox="0 0 14 14"><circle cx="7" cy="7" r="7" fill="#ecebf7"/><path d="M4 7.2l2 2 4-4.4" fill="none" stroke="#6a3df0" stroke-width="1.4"/></svg>Own analytics platform</li>
    <li><svg width="14" height="14" viewBox="0 0 14 14"><circle cx="7" cy="7" r="7" fill="#ecebf7"/><path d="M4 7.2l2 2 4-4.4" fill="none" stroke="#6a3df0" stroke-width="1.4"/></svg>Chat support</li>
    <li><svg width="14" height="14" viewBox="0 0 14 14"><circle cx="7" cy="7" r="7" fill="#ecebf7"/><path d="M4 7.2l2 2 4-4.4" fill="none" stroke="#6a3df0" stroke-width="1.4"/></svg>Optimize hashtags</li>
    <li><svg width="14" height="14" viewBox="0 0 14 14"><circle cx="7" cy="7" r="7" fill="#ecebf7"/><path d="M4 7.2l2 2 4-4.4" fill="none" stroke="#6a3df0" stroke-width="1.4"/></svg>Unlimited users</li>
  </ul>
  <div class="choose">Choose plan</div>
</div>

<div class="plan" style="left:366px;top:2328px">
  <div class="price">$50<small>/month</small></div>
  <div class="name">Base</div>
  <div class="desc">For most businesses that want to otpimize web queries</div>
  <ul>
    <li><svg width="14" height="14" viewBox="0 0 14 14"><circle cx="7" cy="7" r="7" fill="#ecebf7"/><path d="M4 7.2l2 2 4-4.4" fill="none" stroke="#6a3df0" stroke-width="1.4"/></svg>All limited links</li>
    <li><svg width="14" height="14" viewBox="0 0 14 14"><circle cx="7" cy="7" r="7" fill="#ecebf7"/><path d="M4 7.2l2 2 4-4.4" fill="none" stroke="#6a3df0" stroke-width="1.4"/></svg>Own analytics platform</li>
    <li><svg width="14" height="14" viewBox="0 0 14 14"><circle cx="7" cy="7" r="7" fill="#ecebf7"/><path d="M4 7.2l2 2 4-4.4" fill="none" stroke="#6a3df0" stroke-width="1.4"/></svg>Chat support</li>
    <li><svg width="14" height="14" viewBox="0 0 14 14"><circle cx="7" cy="7" r="7" fill="#ecebf7"/><path d="M4 7.2l2 2 4-4.4" fill="none" stroke="#6a3df0" stroke-width="1.4"/></svg>Optimize hashtags</li>
    <li><svg width="14" height="14" viewBox="0 0 14 14"><circle cx="7" cy="7" r="7" fill="#ecebf7"/><path d="M4 7.2l2 2 4-4.4" fill="none" stroke="#6a3df0" stroke-width="1.4"/></svg>Unlimited users</li>
  </ul>
  <div class="choose">Choose plan</div>
</div>

<div class="plan plan-pro">
  <span class="badge">MOST POPULAR</span>
  <div class="price">$100<small>/month</small></div>
  <div class="name">Pro</div>
  <div class="desc">For most businesses that want to otpimize web queries</div>
  <ul>
    <li><svg width="14" height="14" viewBox="0 0 14 14"><circle cx="7" cy="7" r="7" fill="#8a67f5"/><path d="M4 7.2l2 2 4-4.4" fill="none" stroke="#fff" stroke-width="1.4"/></svg>All limited links</li>
    <li><svg width="14" height="14" viewBox="0 0 14 14"><circle cx="7" cy="7" r="7" fill="#8a67f5"/><path d="M4 7.2l2 2 4-4.4" fill="none" stroke="#fff" stroke-width="1.4"/></svg>Own analytics platform</li>
    <li><svg width="14" height="14" viewBox="0 0 14 14"><circle cx="7" cy="7" r="7" fill="#8a67f5"/><path d="M4 7.2l2 2 4-4.4" fill="none" stroke="#fff" stroke-width="1.4"/></svg>Chat support</li>
    <li><svg width="14" height="14" viewBox="0 0 14 14"><circle cx="7" cy="7" r="7" fill="#8a67f5"/><path d="M4 7.2l2 2 4-4.4" fill="none" stroke="#fff" stroke-width="1.4"/></svg>Optimize hashtags</li>
    <li><svg width="14" height="14" viewBox="0 0 14 14"><circle cx="7" cy="7" r="7" fill="#8a67f5"/><path d="M4 7.2l2 2 4-4.4" fill="none" stroke="#fff" stroke-width="1.4"/></svg>Unlimited users</li>
  </ul>
  <div class="choose">Choose plan</div>
</div>

<div class="plan" style="left:859px;top:2328px">
  <div class="price">$200<small>/month</small></div>
  <div class="name">Enterprise</div>
  <div class="desc">For most businesses that want to otpimize web queries</div>
  <ul>
    <li><svg width="14" height="14" viewBox="0 0 14 14"><circle cx="7" cy="7" r="7" fill="#ecebf7"/><path d="M4 7.2l2 2 4-4.4" fill="none" stroke="#6a3df0" stroke-width="1.4"/></svg>All limited links</li>
    <li><svg width="14" height="14" viewBox="0 0 14 14"><circle cx="7" cy="7" r="7" fill="#ecebf7"/><path d="M4 7.2l2 2 4-4.4" fill="none" stroke="#6a3df0" stroke-width="1.4"/></svg>Own analytics platform</li>
    <li><svg width="14" height="14" viewBox="0 0 14 14"><circle cx="7" cy="7" r="7" fill="#ecebf7"/><path d="M4 7.2l2 2 4-4.4" fill="none" stroke="#6a3df0" stroke-width="1.4"/></svg>Chat support</li>
    <li><svg width="14" height="14" viewBox="0 0 14 14"><circle cx="7" cy="7" r="7" fill="#ecebf7"/><path d="M4 7.2l2 2 4-4.4" fill="none" stroke="#6a3df0" stroke-width="1.4"/></svg>Optimize hashtags</li>
    <li><svg width="14" height="14" viewBox="0 0 14 14"><circle cx="7" cy="7" r="7" fill="#ecebf7"/><path d="M4 7.2l2 2 4-4.4" fill="none" stroke="#6a3df0" stroke-width="1.4"/></svg>Unlimited users</li>
  </ul>
  <div class="choose">Choose plan</div>
</div>

<span class="pill" style="left:111px;top:2733px">News</span>
<h2 class="section-title" style="left:111px;top:2795px">Leatest updates on the<br>booking/system</h2>

<article class="news-card" style="left:99px;top:2916px">
  <div class="news-img" role="img" aria-label="Team members joining hands over a desk" style="background:linear-gradient(135deg,#3a4256,#c9b7a6 60%,#e8e6ee)"></div>
  <h4>Better Management of<br>Multi-Function Halls</h4>
  <p>Multi-function halls; for example, a hall can be used for the whole court of basketball or 2 courts of badminton...</p>
  <div class="read-more">Read more</div>
</article>
<article class="news-card" style="left:457px;top:2916px">
  <div class="news-img" role="img" aria-label="Team meeting in a brick-walled office" style="background:linear-gradient(135deg,#8a5a3c,#c79a72 50%,#5d6a7a)"></div>
  <h4>Better Management of<br>Multi-Function Halls</h4>
  <p>Multi-function halls; for example, a hall can be used for the whole court of basketball or 2 courts of badminton...</p>
  <div class="read-more">Read more</div>
</article>
<article class="news-card" style="left:795px;top:2916px">
  <div class="news-img" role="img" aria-label="People gathering on a rooftop terrace" style="background:linear-gradient(160deg,#b9c4d4,#6f7d6a 55%,#4f7a3a)"></div>
  <h4>Better Management of<br>Multi-Function Halls</h4>
  <p>Multi-function halls; for example, a hall can be used for the whole court of basketball or 2 courts of badminton...</p>
  <div class="read-more">Read more</div>
</article>

<svg class="footer-bg" viewBox="0 0 1200 477" aria-hidden="true">
  <defs>
    <linearGradient id="footGrad" x1="0" y1="0" x2="0" y2="1">
      <stop offset="0" stop-color="#6d5ee8"/>
      <stop offset="1" stop-color="#5b22b8"/>
    </linearGradient>
  </defs>
  <path d="M0 80 C150 60 300 0 420 20 C560 45 600 90 760 70 C900 50 1050 60 1200 90 V477 H0 Z" fill="url(#footGrad)"/>
</svg>
<div class="footer-art" role="img" aria-label="Illustrated sports balls" style="left:20px;top:3345px;width:140px;height:100px"></div>
<div class="footer-art" role="img" aria-label="Illustrated sports balls" style="left:1015px;top:3362px;width:165px;height:110px"></div>

<div class="abs footer-brand"><span class="dot"></span>zeitfeldo</div>
<p class="abs footer-tag">Zeitfeldo is the first joint human and AI business with a dedication to developing.</p>

<div class="footer-col" style="left:613px">
  <h5>Links</h5>
  <ul><li>About us</li><li>Servcies</li><li>Demo</li><li>Contact</li></ul>
</div>
<div class="footer-col" style="left:789px">
  <h5>Reach us</h5>
  <ul><li>www.northquill.com</li><li>info@northquill.com</li><li>Tel: +64 4 555 0142</li></ul>
</div>
<div class="footer-col" style="left:964px">
  <h5>Resources</h5>
  <ul><li>Customer portal</li></ul>
</div>

<span class="abs copyright">© 2020-2021 All Rights Reserved.</span>
<span class="abs terms">Terms of Service</span>

</body>
</html>
```